Real Estate agent needs flyer/folder to contain bio and overview of services

I'm including files of the layout of the small folder. The folder is 6 1/2 across and 9 1/2 inches long. It will have a front & back cover and then writing on the 2 inside pages.

I am sending a few files to incorporate into the flyer, 1 new logo to use and 2 files which are coloring ideas.

Colors

Designer to choose colors to be used in the design.

```html
<!DOCTYPE html>
<html lang="en">
<head>
<meta charset="utf-8">
<title>Carla Moretti – Folder Front Cover</title>
<link rel="stylesheet" href="https://fonts.googleapis.com/css2?family=Montserrat:wght@800&family=PT+Serif&display=swap">
<style>
  :root {
    --paper: #ffffff;
    --ink: #111111;
    --royal: #1d3ee8;
    --panel-blue: #0a2fd0;
    --teal: #4ee8d2;
    --sage: #9ba58e;
    --silver-light: #f4f4f4;
    --silver-dark: #b4b4b4;
    --sky: #7fd4f5;
    --cyan: #00f0ff;
  }
  html, body {
    margin: 0;
    padding: 0;
    width: 775px;
    height: 1200px;
    overflow: hidden;
    background: var(--paper);
  }
  .cover {
    position: relative;
    width: 775px;
    height: 1200px;
    background: var(--paper);
    box-sizing: border-box;
    border: 1px solid var(--ink);
    overflow: hidden;
  }
  .cover-art {
    position: absolute;
    inset: 0;
  }
  .tagline {
    position: absolute;
    left: 478px;
    top: 532px;
    margin: 0;
    color: #ffffff;
    font-family: "PT Serif", serif;
    font-size: 26px;
    line-height: 1;
  }
  .tagline-you {
    position: absolute;
    left: 476px;
    top: 560px;
    margin: 0;
    font-family: "Montserrat", sans-serif;
    font-weight: 800;
    font-size: 108px;
    line-height: 1;
    letter-spacing: -2px;
    color: var(--teal);
  }
  .tagline-you .accent { color: var(--sage); }
  .brand {
    position: absolute;
    left: 60px;
    top: 585px;
    display: flex;
    align-items: center;
    gap: 14px;
  }
  .brand-square {
    width: 26px;
    height: 26px;
    background: #cfd8d6;
  }
  .brand-text { text-align: center; }
  .brand-name {
    margin: 0;
    font-family: "PT Serif", serif;
    font-size: 40px;
    line-height: 1.05;
    color: var(--royal);
  }
  .brand-title {
    margin: 6px 0 0;
    font-family: "PT Serif", serif;
    font-size: 11px;
    letter-spacing: 0.5px;
    color: var(--ink);
  }
</style>
</head>
<body>
<main class="cover">
  <svg class="cover-art" width="775" height="1200" viewBox="0 0 775 1200">
    <defs>
      <linearGradient id="silver" x1="0" y1="0" x2="1" y2="0.4">
        <stop offset="0" stop-color="var(--silver-light)"/>
        <stop offset="0.3" stop-color="#ffffff"/>
        <stop offset="0.65" stop-color="var(--silver-dark)"/>
        <stop offset="0.8" stop-color="#eeeeee"/>
        <stop offset="1" stop-color="#9e9e9e"/>
      </linearGradient>
      <linearGradient id="corner-blue" x1="0" y1="0" x2="1" y2="1">
        <stop offset="0" stop-color="#1a7cf0"/>
        <stop offset="1" stop-color="var(--cyan)"/>
      </linearGradient>
      <linearGradient id="mosaic" x1="0" y1="0" x2="1" y2="1">
        <stop offset="0" stop-color="#d8f6fd"/>
        <stop offset="0.5" stop-color="var(--sky)"/>
        <stop offset="1" stop-color="#b6effc"/>
      </linearGradient>
      <linearGradient id="photo" x1="0" y1="0" x2="0" y2="1">
        <stop offset="0" stop-color="#2346d6"/>
        <stop offset="0.5" stop-color="#1c3fbf"/>
        <stop offset="1" stop-color="var(--panel-blue)"/>
      </linearGradient>
      <linearGradient id="towers" x1="0" y1="0" x2="0" y2="1">
        <stop offset="0" stop-color="#ffffff"/>
        <stop offset="1" stop-color="#e6e6e6"/>
      </linearGradient>
      <filter id="band-shadow" x="-10%" y="-10%" width="130%" height="130%">
        <feDropShadow dx="0" dy="8" stdDeviation="6" flood-color="#000" flood-opacity="0.25"/>
      </filter>
      <clipPath id="inside-fold">
        <path d="M0,0 L594,0 Q954,600 594,1200 L0,1200 Z"/>
      </clipPath>
      <clipPath id="outside-fold">
        <path d="M594,0 Q954,600 594,1200 L775,1200 L775,0 Z"/>
      </clipPath>
    </defs>

    <rect role="img" aria-label="Faint illustration of high-rise towers" x="0" y="810" width="720" height="390" fill="url(#towers)" opacity="0.8"/>

    <g clip-path="url(#outside-fold)">
      <rect role="img" aria-label="Light blue triangle mosaic pattern" x="640" y="0" width="135" height="335" fill="url(#mosaic)"/>
      <rect role="img" aria-label="Light blue triangle mosaic pattern" x="640" y="910" width="135" height="290" fill="url(#mosaic)"/>
    </g>

    <polygon class="silver-band" points="0,0 594,0 0,341" fill="url(#silver)" filter="url(#band-shadow)"/>
    <polygon class="corner-accent" points="0,0 92,178 0,231" fill="url(#corner-blue)"/>

    <g clip-path="url(#inside-fold)">
      <path role="img" aria-label="Blue-tinted photo of a community entrance sign with fountains"
            d="M467,407 L775,407 L775,791 L570,791 A140,140 0 0 1 430,651 L430,444 A37,37 0 0 1 467,407 Z"
            fill="url(#photo)"/>
    </g>

    <path class="fold-line" d="M594,0 Q954,600 594,1200" fill="none" stroke="var(--ink)" stroke-width="1"/>
  </svg>

  <div class="brand">
    <div class="brand-square"></div>
    <div class="brand-text">
      <p class="brand-name">Carla Moretti</p>
      <p class="brand-title">REAL ESTATE AGENT</p>
    </div>
  </div>

  <p class="tagline">It's all about</p>
  <p class="tagline-you">Y<span class="accent">O</span>U</p>
</main>
</body>
</html>
```